8x8 Social Media Ad - Brant Summit Expo

Attention Real Estate Agents
Please join us for our
Quarterly Real Estate Training Expo
The 2nd Saturday of February, May, August and November
Our Next Training Expo is _________________________________
From 9 am to 1 pm
at
Halvorne Suites Millbrook Court
4817 Copper Willow Lane, Dunmere, MD 20588
Scheduled Speakers
9:00 am - Marcus Pellington - Orientation
9:30 am - Derrin Oakfield - Multiple Income Streams / Crest Program
10:00 am - Talia Brennick - Marketing though Social Media
10:45 am - Rex Dunmore - Generating Business through Ru-Plaza
11:30 am - Kemi Adeyoro - Real Estate Investing
12:15 pm - Gregor Tamsey - (Main Speaker) Training Topic TBA
For more information call Marcus Pellington at (240) 555-0183 or email mpellington@brantsummithomes.example

```html
<!DOCTYPE html>
<html lang="en">
<head>
<meta charset="utf-8">
<title>Brant Summit Expo – Quarterly Real Estate Training Expo</title>
<link rel="stylesheet" href="https://fonts.googleapis.com/css2?family=Bebas+Neue&family=Poppins:wght@400;500;600;700;800&display=swap">
<style>
  :root {
    --teal: #008b93;
    --teal-deep: #0b5e63;
    --teal-dark: #073f44;
    --ink: #222222;
    --band: #242424;
    --yellow: #ffe800;
    --white: #ffffff;
    --bar: #e9e7e6;
    --photo-a: #3a3f48;
    --photo-b: #9a8677;
  }
  * { margin: 0; padding: 0; box-sizing: border-box; }
  html, body { width: 1200px; height: 1199px; overflow: hidden; background: var(--white); }
  body { font-family: "Poppins", sans-serif; color: var(--ink); }
  .ad { position: relative; width: 1200px; height: 1199px; overflow: hidden; background: var(--white); }
  .abs { position: absolute; }

  .hero-shapes { position: absolute; left: 0; top: 0; }

  .brand { left: 52px; top: 70px; display: flex; align-items: center; gap: 16px; }
  .brand-mark { width: 58px; height: 58px; background: var(--teal); }
  .brand-name { font-weight: 700; font-size: 34px; line-height: 1.1; color: var(--teal); text-transform: uppercase; }

  .date-box { left: 51px; top: 246px; width: 236px; height: 167px; background: var(--teal); color: var(--white); padding: 14px 0 0 28px; }
  .date-day { font-size: 33px; font-weight: 400; line-height: 1; letter-spacing: .5px; }
  .date-num { font-size: 100px; font-weight: 800; line-height: .95; letter-spacing: -3px; }
  .date-num sup { font-size: 62px; vertical-align: top; position: relative; top: 8px; letter-spacing: -1px; }
  .months { left: 307px; top: 236px; font-weight: 800; font-size: 37px; line-height: 45px; text-transform: uppercase; }
  .next-label { left: 50px; top: 447px; font-size: 28px; font-weight: 400; }

  .attention { left: 748px; top: 90px; font-weight: 800; font-size: 60px; color: var(--yellow); line-height: 1; }
  .agents { left: 741px; top: 152px; font-weight: 700; font-size: 30px; color: var(--white); line-height: 1; }
  .megaphone { left: 632px; top: 88px; }
  .join { left: 631px; top: 200px; background: var(--band); color: var(--white); font-size: 17px; font-weight: 500; padding: 4px 8px 3px; }
  .quarterly { left: 632px; top: 237px; color: var(--white); font-size: 27px; font-weight: 400; line-height: 1; }
  .expo-title { left: 629px; top: 275px; color: var(--white); font-family: "Bebas Neue", sans-serif; font-size: 112px; line-height: 93px; letter-spacing: .5px; }

  .info-band { left: 0; top: 540px; width: 1200px; height: 104px; background: var(--band); color: var(--white); }
  .band-icon { position: absolute; }
  .time { left: 134px; top: 22px; font-family: "Bebas Neue", sans-serif; font-size: 64px; line-height: 1; letter-spacing: -1px; white-space: nowrap; }
  .band-divider { left: 523px; top: 28px; width: 1px; height: 54px; background: #6a6a6a; }
  .venue { left: 599px; top: 29px; font-size: 19.5px; line-height: 25px; }

  .speakers-title { left: 0; top: 662px; width: 1200px; text-align: center; font-weight: 800; font-size: 43px; color: var(--teal); letter-spacing: .5px; }
  .speaker { display: flex; align-items: center; gap: 16px; }
  .speaker-photo { width: 105px; height: 105px; border-radius: 50%; border: 2px solid var(--ink); background: linear-gradient(160deg, var(--photo-b), var(--photo-a)); flex: none; }
  .speaker-name { font-weight: 700; font-size: 21px; color: var(--teal); line-height: 1.15; text-transform: uppercase; white-space: nowrap; }
  .speaker-topic { font-size: 17px; line-height: 20px; }
  .speaker-time { font-weight: 700; font-size: 17px; line-height: 22px; }

  .contact-shape { left: 0; top: 0; }
  .contact-lead { left: 68px; top: 1044px; color: var(--white); font-size: 29px; font-weight: 400; }
  .contact-lead b { font-weight: 700; }
  .contact-name { left: 66px; top: 1082px; color: var(--white); font-weight: 800; font-size: 42px; line-height: 1.1; text-transform: uppercase; white-space: nowrap; }
  .contact-icon { position: absolute; }
  .phone { left: 703px; top: 1032px; font-weight: 700; font-size: 38px; line-height: 1; }
  .email { left: 706px; top: 1099px; font-weight: 700; font-size: 19px; line-height: 1; white-space: nowrap; }
</style>
</head>
<body>
<main class="ad">

  <svg class="hero-shapes" width="1200" height="540" viewBox="0 0 1200 540" aria-hidden="true">
    <defs>
      <linearGradient id="hall" x1="0" y1="0" x2="1" y2="1">
        <stop offset="0" stop-color="#0f7b80"/>
        <stop offset=".55" stop-color="#0b5e63"/>
        <stop offset="1" stop-color="#073f44"/>
      </linearGradient>
    </defs>
    <polygon points="487,0 1200,0 1200,540 631,540" fill="var(--band)"/>
    <polygon points="504,0 1200,0 1200,540 648,540" fill="url(#hall)" role="img" aria-label="Seminar hall audience photo in teal tint"/>
    <polygon points="50,488 614,488 624,520 50,520" fill="var(--bar)"/>
  </svg>

  <div class="abs brand">
    <div class="brand-mark"></div>
    <div class="brand-name">Brant Summit<br>Realty Group</div>
  </div>

  <div class="abs date-box">
    <div class="date-day">SATURDAY</div>
    <div class="date-num">2<sup>ND</sup></div>
  </div>
  <div class="abs months">February<br>May<br>August<br>November</div>
  <div class="abs next-label">Our Next Training Expo is</div>

  <svg class="abs megaphone" width="100" height="100" viewBox="0 0 100 100" aria-hidden="true">
    <g fill="none" stroke="#fff" stroke-width="3.5" stroke-linejoin="round" stroke-linecap="round">
      <path d="M18 50 L62 22 L72 70 L24 66 Z"/>
      <ellipse cx="67" cy="46" rx="8" ry="24" transform="rotate(-12 67 46)"/>
      <path d="M12 52 L18 50 L24 66 L16 68 Z"/>
      <path d="M28 66 L36 88 L46 84 L40 68"/>
      <path d="M80 20 L86 12 M84 32 L94 28 M76 10 L78 2"/>
    </g>
  </svg>
  <div class="abs attention">ATTENTION</div>
  <div class="abs agents">REAL ESTATE AGENTS</div>
  <div class="abs join">PLEASE JOIN US FOR OUR</div>
  <div class="abs quarterly">QUARTERLY</div>
  <div class="abs expo-title">REAL ESTATE<br>TRAINING EXPO</div>

  <section class="abs info-band">
    <svg class="band-icon" style="left:74px;top:34px" width="38" height="38" viewBox="0 0 38 38" aria-hidden="true">
      <circle cx="19" cy="19" r="17" fill="none" stroke="var(--teal)" stroke-width="4"/>
      <circle cx="19" cy="19" r="10" fill="none" stroke="var(--teal)" stroke-width="3"/>
      <path d="M19 13 V19 H24" fill="none" stroke="var(--teal)" stroke-width="3" stroke-linecap="round"/>
    </svg>
    <div class="abs time">FROM 9 AM TO 1 PM</div>
    <div class="abs band-divider"></div>
    <svg class="band-icon" style="left:553px;top:28px" width="32" height="44" viewBox="0 0 32 44" aria-hidden="true">
      <path d="M16 2 C8 2 3 8 3 15 C3 24 16 36 16 36 C16 36 29 24 29 15 C29 8 24 2 16 2 Z" fill="var(--teal)"/>
      <circle cx="16" cy="15" r="5" fill="var(--band)"/>
      <ellipse cx="16" cy="39" rx="13" ry="4" fill="none" stroke="var(--teal)" stroke-width="3"/>
    </svg>
    <div class="abs venue">Halvorne Suites Millbrook Court 4817 Copper Willow<br>Lane, Dunmere, MD 20588</div>
  </section>

  <h2 class="abs speakers-title">SCHEDULED SPEAKERS</h2>

  <div class="abs speaker" style="left:51px;top:744px">
    <div class="speaker-photo" role="img" aria-label="Portrait of Marcus Pellington"></div>
    <div><div class="speaker-name">Marcus Pellington</div><div class="speaker-topic">Orientation</div><div class="speaker-time" style="margin-top:6px">9:00 AM</div></div>
  </div>
  <div class="abs speaker" style="left:414px;top:744px">
    <div class="speaker-photo" role="img" aria-label="Portrait of Derrin Oakfield"></div>
    <div><div class="speaker-name">Derrin Oakfield</div><div class="speaker-topic">Multiple Income Streams /<br>Crest Program</div><div class="speaker-time">9:30 AM</div></div>
  </div>
  <div class="abs speaker" style="left:809px;top:744px">
    <div class="speaker-photo" role="img" aria-label="Portrait of Talia Brennick"></div>
    <div><div class="speaker-name">Talia Brennick</div><div class="speaker-topic">Marketing through<br>Social Media</div><div class="speaker-time">10:00 AM</div></div>
  </div>
  <div class="abs speaker" style="left:51px;top:873px">
    <div class="speaker-photo" role="img" aria-label="Portrait of Rex Dunmore"></div>
    <div><div class="speaker-name">Rex Dunmore</div><div class="speaker-topic">Generating Business<br>through Ru-Plaza</div><div class="speaker-time">10:45 AM</div></div>
  </div>
  <div class="abs speaker" style="left:414px;top:873px">
    <div class="speaker-photo" role="img" aria-label="Portrait of Kemi Adeyoro"></div>
    <div><div class="speaker-name">Kemi Adeyoro</div><div class="speaker-topic">Real Estate Investing</div><div class="speaker-time" style="margin-top:6px">11:30 AM</div></div>
  </div>
  <div class="abs speaker" style="left:809px;top:873px">
    <div class="speaker-photo" role="img" aria-label="Portrait of Gregor Tamsey"></div>
    <div><div class="speaker-name">Gregor Tamsey</div><div class="speaker-topic">Training Topic TBA</div><div class="speaker-time" style="margin-top:6px">12:15 AM</div></div>
  </div>

  <svg class="abs contact-shape" width="1200" height="1199" viewBox="0 0 1200 1199" aria-hidden="true">
    <polygon points="0,1022 549,1022 641,1199 0,1199" fill="var(--teal)"/>
  </svg>
  <div class="abs contact-lead">For <b>more information call</b></div>
  <div class="abs contact-name">Marcus Pellington</div>

  <svg class="contact-icon" style="left:643px;top:1034px" width="44" height="44" viewBox="0 0 44 44" aria-hidden="true">
    <circle cx="22" cy="22" r="20" fill="var(--teal)" stroke="var(--ink)" stroke-width="2.5"/>
    <path d="M15 12 L19 12 L21 18 L18 20 C19.5 23.5 21 25 24 26.5 L26 23.5 L32 25.5 L32 29.5 C32 31 30.5 32 29 32 C20 31 13 24 12 15 C12 13.5 13.5 12 15 12 Z" fill="#fff"/>
  </svg>
  <div class="abs phone">(240) 555-0183</div>

  <svg class="contact-icon" style="left:643px;top:1089px" width="44" height="44" viewBox="0 0 44 44" aria-hidden="true">
    <circle cx="22" cy="22" r="20" fill="var(--teal)" stroke="var(--ink)" stroke-width="2.5"/>
    <rect x="12" y="15" width="20" height="14" rx="2" fill="#fff"/>
    <path d="M12.5 16 L22 23 L31.5 16" fill="none" stroke="var(--teal)" stroke-width="2"/>
  </svg>
  <div class="abs email">mpellington@brantsummithomes.example</div>

</main>
</body>
</html>
```